Brindlewick Solutions Ltd

I'd like to create a company letterhead for the attached logo in word format.

I'd like to emphasis the icon in large translucent state from the left corner and ensure that the letterhead colouring matches the colour palette of the current logo with a contrast so it's clear to see. I've attached a copy of our sister company page on the app for reference.

```html
<!DOCTYPE html>
<html lang="en">
<head>
<meta charset="utf-8">
<title>Brindlewick Solutions Ltd — Letterhead</title>
<link rel="stylesheet" href="https://fonts.googleapis.com/css2?family=Arimo:wght@400&family=Montserrat:wght@400;700&family=Open+Sans:wght@400&display=swap">
<style>
  :root {
    --backdrop: #e2e2e2;
    --paper: #ffffff;
    --brand-teal: #0fbfa8;
    --ink: #555555;
    --ink-soft: #8e8e8e;
    --rule: #a9a9a9;
  }
  * { margin: 0; padding: 0; box-sizing: border-box; }
  html, body {
    width: 1200px; height: 1200px; overflow: hidden;
    background: var(--backdrop);
  }
  .letterhead {
    position: absolute;
    left: 233px; top: 81px;
    width: 734px; height: 1037px;
    background: var(--paper);
    box-shadow: 2px 3px 5px rgba(0,0,0,0.28);
  }
  .brand {
    position: absolute;
    top: 56px; left: 0; right: 0;
    display: flex; justify-content: center; align-items: center; gap: 12px;
  }
  .brand-dot {
    width: 40px; height: 40px; border-radius: 50%;
    background: var(--brand-teal);
  }
  .brand-name {
    font-family: "Montserrat", sans-serif;
    font-weight: 400;
    font-size: 28px;
    color: var(--brand-teal);
    letter-spacing: 0.2px;
  }
  .salutation {
    position: absolute; left: 67px; top: 318px;
    font-family: "Montserrat", sans-serif;
    font-weight: 700; font-size: 16.5px;
    color: var(--ink);
  }
  .letter-body {
    position: absolute; left: 66px; top: 366px; width: 610px;
    font-family: "Arimo", sans-serif;
    font-size: 12.4px; line-height: 15.2px;
    color: var(--ink);
    white-space: nowrap;
  }
  .letter-body p { margin-bottom: 13px; }
  .closing {
    position: absolute; left: 67px; top: 678px;
    font-family: "Montserrat", sans-serif;
    font-weight: 700; font-size: 9.5px;
    color: var(--ink);
  }
  .signature {
    position: absolute; left: 85px; top: 725px;
    font-family: "Open Sans", sans-serif;
    font-size: 18px; letter-spacing: -1.2px;
    color: var(--ink);
  }
  .contact-footer {
    position: absolute; left: 0; right: 0; top: 984px;
    font-family: "Arimo", sans-serif;
    font-size: 11.2px; color: var(--ink-soft);
  }
  .address-line {
    display: flex; justify-content: center; align-items: center; gap: 6px;
  }
  .address-line .rule {
    width: 90px; height: 1px; background: var(--rule);
  }
  .contact-line {
    margin-top: 3px;
    display: flex; justify-content: center; align-items: center; gap: 9px;
  }
  .contact-item { display: flex; align-items: center; gap: 6px; }
  .contact-item svg { width: 10px; height: 10px; fill: var(--brand-teal); }
  .brand-band {
    position: absolute; left: 0; right: 0; bottom: 0;
    height: 7px; background: var(--brand-teal);
  }
</style>
</head>
<body>
  <main class="letterhead">
    <header class="brand">
      <span class="brand-dot"></span>
      <span class="brand-name">Brindlewick Solutions Ltd</span>
    </header>

    <h1 class="salutation">Dear Mr. Hadley,</h1>

    <section class="letter-body">
      <p>Lorem ipsum dolor sit amet, consectetuer adipiscing elit, sed diam nonmmy nibh euismod tincidunt ut laor<br>eet dolore magna aliquam erat volutpat. Ut wisi enim ad minim veniam, quis nostrud exerci tationmcorper<br>suscipit lobortis nisl ut aliquip ex ea commodo consequat. Duis autem vel eum iriure dolor in hendrerit in<br>vulputate velit esse molestie consequat, vel illum dolore eu feugiat</p>
      <p>Rorem ipsum dolor sit amet, consectetuer adipiscing elit, sed diam nonmmy nibh euismod tincidunt ut laor<br>eet dolore magna aliquam erat volutpat. Ut wisi enim ad minim veniam, quis nostrud exerci tationmcorper<br>suscipit lobortis nisl ut aliquip ex ea commodo consequat. Duis autem vel eum iriure dolor in hendrerit in<br>vulputate velit esse molest</p>
      <p>Dorem ipsum dolor sit amet, consectetuer adipiscing elit, sed diam nonmmy nibh euismod tincidunt ut laor<br>eet dolore magna aliquam erat volutpat. Ut wisi enim ad minim veniam, quis nostrud exerci tationmcorper<br>suscipit lobortis nisl ut aliquip ex ea commodo consequat. Duis autem vel eum iriure dolor in hendrerit in<br>suscipit lobortis nisl ut aliquip ex ea commodo consequat. Duis autem vel eum iriure dolor in hendrerit in<br>vulputate velit esse molestie consequat, vel illum</p>
      <p>Sorem ipsum dolor sit amet, consectetuer adipiscing elit, sed diam nonmmy nibh euismod tincidunt ut laor<br>eet dolore magna aliquam erat volutpat. Ut wisi enim ad minim veniam, quis nostrud exerci tationmcorper<br>suscipit lobortis nisl ut aliquip ex ea commodo consequat. Duis autem vel eum iriure dolor in</p>
    </section>

    <p class="closing">Sincerely,</p>
    <p class="signature">Corwin Ashby</p>

    <footer class="contact-footer">
      <div class="address-line">
        <span class="rule"></span>
        <span>Your address, city, state, ZIP 0000</span>
        <span class="rule"></span>
      </div>
      <div class="contact-line">
        <span class="contact-item">
          <svg viewBox="0 0 10 10" aria-hidden="true"><path d="M2 0.5 L3.6 2.6 L2.8 3.6 Q3.8 5.8 6.2 7 L7.3 6.2 L9.5 7.8 L8.4 9.4 Q4.5 9.6 1.6 6.5 Q-0.3 3.6 0.6 1.4 Z"/></svg>
          123-456-2100
        </span>
        <span class="contact-item">
          <svg viewBox="0 0 10 10" aria-hidden="true"><path d="M0 2 H10 V8.5 H0 Z M0.6 2.4 L5 5.6 L9.4 2.4 V2.8 L5 6.2 L0.6 2.8 Z" fill-rule="evenodd"/></svg>
          hello@brindlewick.co
        </span>
        <span class="contact-item">
          <svg viewBox="0 0 10 10" aria-hidden="true"><circle cx="5" cy="5" r="4.8"/><path d="M1 4 H9 M1 6 H9 M5 0.3 Q2.6 5 5 9.7 M5 0.3 Q7.4 5 5 9.7" stroke="#fff" stroke-width="0.7" fill="none"/></svg>
          www.brindlewick.co
        </span>
      </div>
    </footer>

    <div class="brand-band"></div>
  </main>
</body>
</html>
```